Veldmark Supplies Business Card

Professional business card that stand out to our potential customers. Front and back with clean modern design

Industry/Entity Type

Oil and gas

Contact Information for Business Card

Name, address, website , office phone and cell number

Requirements
Must have
• Editable files for each employee

```html
<!DOCTYPE html>
<html lang="en">
<head>
<meta charset="utf-8">
<title>Veldmark Supplies Business Card</title>
<link href="https://fonts.googleapis.com/css2?family=Roboto:wght@400;700&display=swap" rel="stylesheet">
<style>
  :root {
    --bg: #d2d3d5;
    --card: #ffffff;
    --red: #ea1d24;
    --blue: #00a9d1;
    --ink: #222222;
  }
  * { margin: 0; padding: 0; box-sizing: border-box; }
  html, body { width: 900px; height: 1200px; overflow: hidden; }
  body { background: var(--bg); font-family: "Roboto", Arial, sans-serif; color: var(--ink); position: relative; }

  .card { position: absolute; left: 134px; width: 632px; height: 364px; background: var(--card); overflow: hidden; }
  .card-front { top: 210px; }
  .card-back { top: 624px; }

  .brand { display: flex; align-items: center; gap: 10px; font-weight: 700; color: var(--red); white-space: nowrap; }
  .brand-square { background: var(--blue); flex: none; }

  .card-front .brand { position: absolute; left: 0; right: 0; top: 160px; justify-content: center; font-size: 34px; }
  .card-front .brand-square { width: 30px; height: 30px; }

  .card-back .brand { position: absolute; left: 58px; top: 168px; font-size: 21px; gap: 8px; }
  .card-back .brand-square { width: 18px; height: 18px; }

  .divider { position: absolute; left: 316px; width: 2px; }
  .divider-top { top: 99px; height: 38px; background: var(--red); }
  .divider-mid { top: 139px; height: 90px; background: var(--blue); }
  .divider-bot { top: 233px; height: 36px; background: var(--red); }

  .contact { position: absolute; left: 346px; top: 97px; }
  .person-name { font-size: 25px; font-weight: 700; line-height: 1; letter-spacing: -0.2px; }
  .person-first { color: var(--red); }
  .person-last { color: var(--blue); }
  .person-role { font-size: 15px; margin-top: 8px; line-height: 1; }
  .address { font-size: 15px; line-height: 20px; margin-top: 10px; }
  .contact-list { list-style: none; margin-top: 8px; }
  .contact-list li { display: flex; align-items: center; gap: 8px; font-size: 15px; height: 25px; }
  .contact-list svg { width: 15px; height: 15px; flex: none; }
  .phone-number { letter-spacing: 2.4px; }

  .footer-band { position: absolute; left: 0; bottom: 0; width: 100%; height: 13px; }
</style>
</head>
<body>

<section class="card card-front" aria-label="Card front">
  <div class="brand"><span class="brand-square"></span>Veldmark Supplies</div>
</section>

<section class="card card-back" aria-label="Card back">
  <div class="brand"><span class="brand-square"></span>Veldmark Supplies</div>

  <span class="divider divider-top"></span>
  <span class="divider divider-mid"></span>
  <span class="divider divider-bot"></span>

  <div class="contact">
    <p class="person-name"><span class="person-first">Aren</span> <span class="person-last">Voskuil</span></p>
    <p class="person-role">CEO</p>
    <p class="address">417 N.Harlow Suite 6<br>Brackton, Tx 79742</p>
    <ul class="contact-list">
      <li>
        <svg viewBox="0 0 24 24" aria-hidden="true"><path fill="var(--blue)" d="M6.6 10.8c1.4 2.8 3.8 5.1 6.6 6.6l2.2-2.2c.3-.3.7-.4 1-.2 1.1.4 2.3.6 3.6.6.6 0 1 .4 1 1V20c0 .6-.4 1-1 1C10.6 21 3 13.4 3 4c0-.6.4-1 1-1h3.5c.6 0 1 .4 1 1 0 1.3.2 2.5.6 3.6.1.3 0 .7-.2 1L6.6 10.8z"/></svg>
        <span class="phone-number">(555)204-7319</span>
      </li>
      <li>
        <svg viewBox="0 0 24 24" aria-hidden="true"><rect x="2" y="5" width="20" height="14" fill="var(--blue)"/><path d="M2 5l10 8 10-8M2 19l8-7M22 19l-8-7" fill="none" stroke="#fff" stroke-width="1.6"/></svg>
        <span>sales@veldmarksupplies.com</span>
      </li>
      <li>
        <svg viewBox="0 0 24 24" aria-hidden="true"><g fill="none" stroke="var(--blue)" stroke-width="1.8"><circle cx="12" cy="12" r="9.5"/><ellipse cx="12" cy="12" rx="4" ry="9.5"/><path d="M2.5 12h19M4 7h16M4 17h16"/></g></svg>
        <span>www.veldmarksupplies.com</span>
      </li>
    </ul>
  </div>

  <svg class="footer-band" viewBox="0 0 632 13" preserveAspectRatio="none" aria-hidden="true">
    <polygon points="0,0 324,0 319,13 0,13" fill="var(--red)"/>
    <polygon points="328,0 632,0 632,13 323,13" fill="var(--blue)"/>
  </svg>
</section>

</body>
</html>
```